Medical Practice needs a Letterhead Design

We need a clean, modern letterhead design for our stem cell medical practice.

Industry/Entity Type

Medical

```html
<!DOCTYPE html>
<html lang="en">
<head>
<meta charset="utf-8">
<title>VitaCore Medical Letterhead</title>
<link href="https://fonts.googleapis.com/css2?family=Josefin+Sans:wght@700&display=swap" rel="stylesheet">
<style>
  :root {
    --navy: #0e3449;
    --lime: #a9c23f;
    --paper: #ffffff;
    --ink: #0e3449;
  }
  html, body {
    margin: 0;
    padding: 0;
    overflow: hidden;
    background: var(--paper);
  }
  .letterhead {
    position: relative;
    width: 927px;
    height: 1200px;
    background: var(--paper);
    overflow: hidden;
    font-family: "Josefin Sans", sans-serif;
    font-weight: 700;
    color: var(--ink);
  }
  .header-band {
    position: absolute;
    left: 0;
    top: 0;
    width: 927px;
    height: 111px;
    background: var(--navy);
  }
  .brand-disc {
    position: absolute;
    left: 379px;
    top: 36px;
    width: 168px;
    height: 168px;
    border-radius: 50%;
    background: var(--paper);
  }
  .brand-dot {
    position: absolute;
    left: 453px;
    top: 64px;
    width: 20px;
    height: 20px;
    border-radius: 50%;
    background: var(--lime);
  }
  .brand-name {
    position: absolute;
    left: 379px;
    top: 104px;
    width: 168px;
    text-align: center;
    font-size: 19px;
    line-height: 24px;
    letter-spacing: 1px;
    color: var(--navy);
  }
  .brand-name span { display: block; }
  .contact-line {
    position: absolute;
    top: 116px;
    font-size: 11.5px;
    font-variant: small-caps;
    letter-spacing: 1.8px;
    white-space: nowrap;
  }
  .contact-address { left: 77px; }
  .contact-phone { left: 549px; }
  .contact-fax { left: 714px; }
  .footer-dot {
    position: absolute;
    left: 451px;
    top: 1098px;
    width: 24px;
    height: 24px;
    border-radius: 50%;
    background: var(--lime);
  }
  .footer-url {
    position: absolute;
    left: 0;
    width: 927px;
    top: 1158px;
    text-align: center;
    font-size: 13px;
    letter-spacing: 2px;
  }
</style>
</head>
<body>
  <div class="letterhead">
    <div class="header-band"></div>
    <div class="brand-disc"></div>
    <div class="brand-dot"></div>
    <div class="brand-name">
      <span>VitaCore</span>
      <span>Medical</span>
    </div>
    <div class="contact-line contact-address">5678 Harbor Lane, Westfield, CA 90000</div>
    <div class="contact-line contact-phone">Phone: (555)010-2020</div>
    <div class="contact-line contact-fax">Fax: (555)010-2030</div>
    <div class="footer-dot"></div>
    <div class="footer-url">WWW.VITACORECLINIC.ORG</div>
  </div>
</body>
</html>
```